Silver Heron Motor Works needs a logo design

I'm after a logo design for a new Female owned automotive repair workshop in the Queanbeyan/Canberra Australia Area.
We offer repairs on all passenger cars, 4wds and light trucks emphasising a strong honest work ethic and a genuine interest in the customer and their vehicles needs. With business details on the front of the card and what we offer on the back.
I would like a design with a phoenix in multiple colours maybe hovering over a flaming wheel or a car with wheels flaming with the phoenix hovering up out of the flames
All Vehicle users
Automotive
On the front
Silver Heron Motor
Marla Pettigrew Owner/ Mechanic 0481736055
email marla@silverheronmotor.com.au
Website www.silverheronmotorworks.com.au
On the back
All Cars, 4WDs, Light trucks, makes and models
Log book servicing
General vehicle servicing
Major vehicle servicing
brake and clutch servicing and repairs
Suspension repairs
cooling systems
All major and minor mechanical repairs
minor electrical rewiring and repairs
Designer to choose colors to be used in the design.

```html
<!DOCTYPE html>
<html lang="en">
<head>
<meta charset="utf-8">
<title>Silver Heron Motor Works – Business Card</title>
<link rel="stylesheet" href="https://fonts.googleapis.com/css2?family=Cormorant+Garamond:wght@500;600&family=Pinyon+Script&display=swap">
<style>
  :root {
    --backdrop: #d9dadc;
    --card-black: #070505;
    --card-deep: #1c0c07;
    --glow-core: #8a4318;
    --glow-mid: #4a1c0a;
    --accent-orange: #e2671f;
    --text-cream: #f1e6cf;
    --text-white: #f4f1ec;
    --watermark: rgba(120, 50, 25, 0.22);
    --star: #f6eccc;
  }
  * { box-sizing: border-box; margin: 0; padding: 0; }
  html, body {
    width: 1200px; height: 1200px; overflow: hidden;
    background: var(--backdrop);
  }
  .sheet {
    width: 1200px; height: 1200px;
    display: flex; flex-direction: column; align-items: center; justify-content: center;
    gap: 60px;
  }
  .card {
    position: relative;
    width: 820px; height: 500px;
    overflow: hidden;
    background: radial-gradient(ellipse at 70% 55%, var(--card-deep) 0%, var(--card-black) 65%);
    box-shadow: 0 6px 18px rgba(0,0,0,0.25);
    font-family: "Cormorant Garamond", serif;
  }
  .artwork-area {
    position: absolute;
    background: radial-gradient(closest-side, var(--glow-core) 0%, var(--glow-mid) 55%, rgba(7,5,5,0) 100%);
  }
  .card-front .artwork-area { left: 30px; top: 40px; width: 420px; height: 420px; }
  .card-back .artwork-area { left: 660px; top: 170px; width: 380px; height: 380px; }

  .watermark {
    position: absolute; left: 470px; top: 222px;
    font-weight: 500;
    font-size: 54px; line-height: 58px;
    color: var(--watermark);
  }
  .owner-name {
    position: absolute; right: 50px; top: 86px;
    font-family: "Pinyon Script", cursive; font-weight: 400;
    font-size: 56px; color: var(--accent-orange);
  }
  .owner-role {
    position: absolute; right: 60px; top: 168px;
    font-size: 26px; font-weight: 500; color: var(--text-white);
  }
  .contact {
    position: absolute; right: 50px; bottom: 48px;
    list-style: none; text-align: right;
    font-size: 25px; font-weight: 500; color: var(--text-white);
  }
  .contact li { display: flex; align-items: center; justify-content: flex-end; gap: 12px; height: 38px; }
  .contact svg { width: 24px; height: 24px; fill: var(--accent-orange); }

  .services {
    position: absolute; left: 46px; top: 40px;
    list-style: none;
    font-size: 23px; font-weight: 500; color: var(--text-cream);
  }
  .services li { display: flex; align-items: center; gap: 16px; height: 42px; }
  .services svg { width: 18px; height: 18px; fill: var(--star); flex: none; }
</style>
</head>
<body>
<main class="sheet">
  <section class="card card-front" aria-label="Card front">
    <div class="artwork-area" role="img" aria-label="Illustration of an alloy wheel engulfed in flames"></div>
    <p class="watermark">silver heron<br>motor</p>
    <h1 class="owner-name">Marla Pettigrew</h1>
    <p class="owner-role">Owner/ Mechanic</p>
    <ul class="contact">
      <li>0481736055
        <svg viewBox="0 0 24 24" aria-hidden="true"><path d="M6.6 10.8a15.1 15.1 0 0 0 6.6 6.6l2.2-2.2a1 1 0 0 1 1-.25 11.4 11.4 0 0 0 3.6.57 1 1 0 0 1 1 1V20a1 1 0 0 1-1 1A17 17 0 0 1 3 4a1 1 0 0 1 1-1h3.5a1 1 0 0 1 1 1c0 1.25.2 2.45.57 3.57a1 1 0 0 1-.25 1z"/></svg>
      </li>
      <li>marla@silverheronmotor.com.au
        <svg viewBox="0 0 24 24" aria-hidden="true"><path d="M2 5h20v14H2z M3.5 6.5 12 13l8.5-6.5" fill="var(--accent-orange)" stroke="var(--card-black)" stroke-width="1.2"/></svg>
      </li>
    </ul>
  </section>

  <section class="card card-back" aria-label="Card back">
    <div class="artwork-area" role="img" aria-label="Illustration of an alloy wheel engulfed in flames"></div>
    <ul class="services">
      <li><svg viewBox="0 0 24 24" aria-hidden="true"><path d="M12 2l2.9 6.9 7.1.6-5.4 4.7 1.6 7.3L12 17.8 5.8 21.5l1.6-7.3L2 9.5l7.1-.6z"/></svg>All Cars, 4wds, Light Trucks, Makes And Models</li>
      <li><svg viewBox="0 0 24 24" aria-hidden="true"><path d="M12 2l2.9 6.9 7.1.6-5.4 4.7 1.6 7.3L12 17.8 5.8 21.5l1.6-7.3L2 9.5l7.1-.6z"/></svg>Log Book Servicing</li>
      <li><svg viewBox="0 0 24 24" aria-hidden="true"><path d="M12 2l2.9 6.9 7.1.6-5.4 4.7 1.6 7.3L12 17.8 5.8 21.5l1.6-7.3L2 9.5l7.1-.6z"/></svg>General Vehicle Servicing</li>
      <li><svg viewBox="0 0 24 24" aria-hidden="true"><path d="M12 2l2.9 6.9 7.1.6-5.4 4.7 1.6 7.3L12 17.8 5.8 21.5l1.6-7.3L2 9.5l7.1-.6z"/></svg>Major Vehicle Servicing</li>
      <li><svg viewBox="0 0 24 24" aria-hidden="true"><path d="M12 2l2.9 6.9 7.1.6-5.4 4.7 1.6 7.3L12 17.8 5.8 21.5l1.6-7.3L2 9.5l7.1-.6z"/></svg>Brake And Clutch Servicing And Repairs</li>
      <li><svg viewBox="0 0 24 24" aria-hidden="true"><path d="M12 2l2.9 6.9 7.1.6-5.4 4.7 1.6 7.3L12 17.8 5.8 21.5l1.6-7.3L2 9.5l7.1-.6z"/></svg>Suspension Repairs</li>
      <li><svg viewBox="0 0 24 24" aria-hidden="true"><path d="M12 2l2.9 6.9 7.1.6-5.4 4.7 1.6 7.3L12 17.8 5.8 21.5l1.6-7.3L2 9.5l7.1-.6z"/></svg>Cooling Systems</li>
      <li><svg viewBox="0 0 24 24" aria-hidden="true"><path d="M12 2l2.9 6.9 7.1.6-5.4 4.7 1.6 7.3L12 17.8 5.8 21.5l1.6-7.3L2 9.5l7.1-.6z"/></svg>All Major And Minor Mechanical Repairs</li>
      <li><svg viewBox="0 0 24 24" aria-hidden="true"><path d="M12 2l2.9 6.9 7.1.6-5.4 4.7 1.6 7.3L12 17.8 5.8 21.5l1.6-7.3L2 9.5l7.1-.6z"/></svg>Minor Electrical Rewiring And Repairs</li>
    </ul>
  </section>
</main>
</body>
</html>
```